Landscape Construction and Design Company

We are a landscape construction and design company from New Jersey. We design and install landscapes and hardscapes for residential properties. The name of the company is Belwick's Landscape and Design LLC. We specialize mostly in planting trees and stone work, some water features. We would like to see design themes that include a tree or trees and a stone walkway or wall. We like earth tone colors. We like traditional to modern designs.

Target Market(s)

Homeowners

Industry/Entity Type

Landscape

Contact Information for Business Card

Nature themed design, earth tone colors, space for company name, address, phone numbers, email and website address

Logo Text

No text

Font styles to use
Serif

Colors

Designer to choose colors to be used in the design.

Requirements
Must have
• A tree or trees, similar to the ones uploaded in my supporting images
Nice to have
• I like trees similar to those in my uploaded supporting images. I like artistic, nature theme, earth tone colors
Should not have
• Pictures of real landscapes, cartoon looking logo or objects

```html
<!DOCTYPE html>
<html lang="en">
<head>
<meta charset="utf-8">
<title>Belwick's Landscape and Design LLC – Business Card</title>
<link rel="stylesheet" href="https://fonts.googleapis.com/css2?family=Playfair+Display:wght@700&family=Patrick+Hand&display=swap">
<style>
  :root {
    --page: #ffffff;
    --leaf: #9dbd2e;
    --olive: #8ba661;
    --moss: #9bb279;
    --fern: #6a9a3c;
    --forest: #436427;
    --cream: #eff4cc;
    --bark: #6f4a25;
    --bark-dark: #4a2a12;
    --brand-green: #0f6b36;
    --logo-mark: #7d7d78;
    --caption-green: #3b5e1f;
    --hand: "Patrick Hand", cursive;
    --serif: "Playfair Display", serif;
  }
  * { margin: 0; padding: 0; box-sizing: border-box; }
  html, body { width: 1200px; height: 1015px; overflow: hidden; background: var(--page); }
  .canvas { position: relative; width: 1200px; height: 1015px; }

  .card-shadow {
    position: absolute; left: 190px; top: 598px; width: 820px; height: 50px;
    background: radial-gradient(ellipse at center, rgba(0,0,0,0.16) 0%, rgba(0,0,0,0) 70%);
  }
  .business-card {
    position: absolute; left: 167px; top: 88px; width: 866px; height: 529px;
    border-radius: 42px 42px 0 0; overflow: hidden;
  }
  .business-card svg { display: block; width: 100%; height: 100%; }

  .brand-name { font-family: var(--serif); font-weight: 700; fill: var(--brand-green); }
  .contact-text { font-family: var(--hand); font-size: 47px; fill: var(--bark-dark); }

  .caption {
    position: absolute; left: 0; width: 1200px; text-align: center;
    font-family: var(--hand); color: var(--caption-green);
  }
  .caption-icons { top: 734px; font-size: 33px; }
  .caption-logo { top: 916px; font-size: 35px; }

  .icon-showcase { position: absolute; top: 772px; height: 104px; }
  .icon-pin { left: 376px; width: 52px; }
  .icon-phone { left: 555px; width: 72px; }
  .icon-mail { left: 742px; width: 82px; }

  .flourish {
    position: absolute; left: 334px; top: 994px; width: 532px; height: 6px;
    border-radius: 3px; background: var(--bark-dark); opacity: 0.8;
  }
</style>
</head>
<body>
<main class="canvas">
  <div class="card-shadow"></div>

  <section class="business-card" aria-label="Business card">
    <svg viewBox="0 0 938 573" xmlns="http://www.w3.org/2000/svg">
      <rect width="938" height="573" fill="var(--leaf)"/>
      <path d="M0,0 H390 C250,25 110,80 0,180 Z" fill="var(--olive)"/>
      <path d="M0,265 C120,250 260,300 420,330 L520,420 L0,450 Z" fill="var(--forest)"/>
      <path d="M0,290 C150,285 330,330 560,450 L0,470 Z" fill="var(--moss)"/>
      <path d="M938,115 C820,110 720,150 640,240 L600,470 L938,450 Z" fill="var(--forest)"/>
      <path d="M938,320 C820,360 700,400 560,470 L938,460 Z" fill="var(--fern)"/>
      <path d="M0,447 L560,485 L938,445 V573 H0 Z" fill="var(--cream)"/>

      <path class="frame" d="M96,82 L469,48 L842,82 Q852,84 852,100 V385 Q852,398 838,402 L469,433 L100,402 Q86,398 86,385 V100 Q86,84 96,82 Z"
            fill="var(--cream)" stroke="var(--bark)" stroke-width="20" stroke-linejoin="round"/>

      <g role="img" aria-label="Small curl ornaments in the frame corners" fill="var(--bark)" opacity="0.55">
        <circle cx="130" cy="130" r="9"/>
        <circle cx="808" cy="130" r="9"/>
        <circle cx="130" cy="350" r="9"/>
        <circle cx="808" cy="350" r="9"/>
      </g>

      <g class="brand-block">
        <text class="brand-name" x="180" y="268" font-size="104" textLength="480" lengthAdjust="spacingAndGlyphs">BELWICK'S</text>
        <circle class="logo-placeholder" role="img" aria-label="Place for the company logo mark" cx="716" cy="226" r="44" fill="var(--logo-mark)"/>
        <text class="brand-name" x="180" y="304" font-size="30" textLength="570" lengthAdjust="spacing">LANDSCAPE &amp; DESIGN</text>
        <text class="brand-name" x="469" y="392" text-anchor="middle" font-size="28">LLC.</text>
      </g>

      <g class="contact contact-address">
        <path d="M42,478 C30,478 24,487 24,496 C24,508 36,518 42,532 C48,518 60,508 60,496 C60,487 54,478 42,478 Z" fill="var(--bark-dark)"/>
        <circle cx="42" cy="495" r="5" fill="var(--cream)"/>
        <text class="contact-text" x="64" y="522" transform="rotate(4 64 522)" textLength="216" lengthAdjust="spacingAndGlyphs">Your address</text>
      </g>
      <g class="contact contact-phone">
        <path d="M346,500 C338,504 336,520 344,530 C350,538 358,540 364,536 L360,526 L354,528 C350,524 348,516 350,510 L356,508 Z" fill="var(--bark-dark)"/>
        <path d="M340,494 Q334,486 340,478 M334,498 Q326,486 334,472" stroke="var(--bark-dark)" stroke-width="2" fill="none"/>
        <text class="contact-text" x="373" y="540" textLength="240" lengthAdjust="spacingAndGlyphs">Phone number</text>
      </g>
      <g class="contact contact-mail" fill="none" stroke="var(--bark-dark)" stroke-width="4" stroke-linejoin="round">
        <rect x="657" y="496" width="42" height="30" rx="3"/>
        <path d="M659,498 L678,514 L697,498"/>
        <path d="M680,494 C680,486 684,482 688,480" stroke-width="3"/>
        <text class="contact-text" x="706" y="526" transform="rotate(-4 706 526)" stroke="none" fill="var(--bark-dark)" textLength="198" lengthAdjust="spacingAndGlyphs">Your e-mail</text>
      </g>
    </svg>
  </section>

  <p class="caption caption-icons">personalised icons</p>

  <svg class="icon-showcase icon-pin" viewBox="0 0 52 104" aria-label="Location pin icon">
    <path d="M26,4 C12,4 4,15 4,26 C4,42 18,52 26,76 C34,52 48,42 48,26 C48,15 40,4 26,4 Z" fill="var(--bark-dark)"/>
    <circle cx="26" cy="24" r="7" fill="var(--page)"/>
  </svg>
  <svg class="icon-showcase icon-phone" viewBox="0 0 72 104" aria-label="Phone icon">
    <path d="M30,36 C18,42 16,66 28,82 C36,94 50,98 58,92 C62,89 60,84 56,80 C52,76 48,78 44,80 C38,76 34,64 36,56 C42,54 46,50 44,44 C42,38 36,32 30,36 Z" fill="var(--bark-dark)"/>
    <path d="M22,32 Q16,22 24,12 M12,36 Q4,18 18,4" stroke="var(--bark-dark)" stroke-width="2" fill="none"/>
  </svg>
  <svg class="icon-showcase icon-mail" viewBox="0 0 82 104" aria-label="E-mail icon">
    <g fill="none" stroke="var(--bark-dark)" stroke-width="6" stroke-linejoin="round">
      <path d="M4,42 L76,38 L78,94 L6,96 Z"/>
      <path d="M6,44 L40,72 L76,40"/>
      <path d="M44,36 C42,24 44,14 50,6" stroke-width="3"/>
    </g>
  </svg>

  <p class="caption caption-logo">minimal artistic logo design</p>
  <div class="flourish" role="img" aria-label="Hand-drawn curl flourish underline"></div>
</main>
</body>
</html>
```